Keystonery Billboard - Financial Services Company (Investments, Tax Planning and Insurance)

Our new office has a billboard directly above the office building. We'd like something eye-catching with a strong Call to Action, with the main part of the billboard being under 7 words if possible. We'd like you to include a way to get ahold of us (either our website keystoneryllc.example or our phone number 302-418-2907. You may also include in small font something to indicate that we've been serving the area since 1980 (the DE area, the tri-state area, the Marlowe Hollow, etc.)

We offer financial planning, tax planning, and insurance, and we help our clients to focus on their goals and happiness by providing everything they need for lifelong wealth under one roof.

Our logos are attached, we use a triangle logo with green and gray. We use the tagline "discover lasting prosperity" but this does not need to be included.

Potential ideas we have seen from other financial companies-
- the concept that the driver spends more time looking at billboards than planning for their retirement
-something along the lines of "everything you need for your finances is in this building right here" planning, investments, taxes, insurance"
-don't spend your time worrying about retirement, let us help you plan for it
-are you working for your money, or is it working for you?
- retirement takes planning, we're here to help
- ready to retire? talk to us
- need investment advice?
- need help investing?
- crossing your fingers isn't a retirement plan. we can help.
- retiring soon? you need help.

Those are just general ideas, please feel free to be creative.

brand colors:
#00b585
#00b185
#000000
#ffffff
#6d6f75
#6d6f75
#6f7074
#021712
#052e24

```html
<!DOCTYPE html>
<html lang="en">
<head>
<meta charset="utf-8">
<title>Keystonery Billboard</title>
<link rel="stylesheet" href="https://fonts.googleapis.com/css2?family=Tinos:wght@400;700&family=Montserrat:wght@500;700&display=swap">
<style>
  :root {
    --green-deep: #0a6844;
    --green-bright: #00a063;
    --green-brand: #00a866;
    --grey-text: #6d6f75;
    --ink-bar: #2a2a2a;
    --white: #ffffff;
    --page: #d6d6d6;
    --cell-light: #ffffff;
    --cell-shade: #e6e6e6;
  }
  * { box-sizing: border-box; margin: 0; padding: 0; }
  html, body { width: 1000px; height: 1200px; overflow: hidden; }
  body { background: var(--page); position: relative; }

  .billboard {
    position: absolute; left: 20px; top: 360px;
    width: 960px; height: 480px;
    background: var(--white);
    overflow: hidden;
    box-shadow: 0 12px 30px rgba(0,0,0,.25);
  }
  .billboard__shapes { position: absolute; left: 0; top: 0; }

  .brand {
    position: absolute; left: 44px; top: 14px;
    font-family: "Tinos", serif;
  }
  .brand__name {
    font-size: 38px; font-weight: 400; color: var(--green-brand);
    line-height: 1; letter-spacing: -0.5px;
  }
  .brand__tagline {
    font-family: "Montserrat", sans-serif;
    font-size: 7px; font-weight: 500; letter-spacing: 3px;
    color: var(--grey-text); text-transform: uppercase; margin-top: 3px;
  }

  .headline {
    position: absolute; left: 44px; top: 91px;
    font-family: "Tinos", serif; font-weight: 700;
    font-size: 45px; line-height: 51px; color: var(--white);
  }

  .services {
    position: absolute; left: 0; top: 267px; width: 960px; height: 78px;
    display: flex;
  }
  .service {
    display: flex; align-items: center; gap: 14px;
    padding-left: 53px; height: 100%;
    background: linear-gradient(90deg, var(--cell-light) 0%, var(--cell-shade) 100%);
    font-family: "Tinos", serif; font-weight: 700;
    font-size: 29px; color: var(--grey-text);
  }
  .service--planning { width: 253px; padding-left: 53px; }
  .service--investments { width: 253px; padding-left: 13px; }
  .service--taxes { width: 172px; padding-left: 13px; }
  .service--insurance { width: 282px; padding-left: 14px; }
  .service__icon { width: 54px; height: 54px; flex: none; }

  .contact-bar {
    position: absolute; left: 0; top: 345px; width: 960px; height: 70px;
    background: var(--ink-bar);
    display: flex; align-items: center; justify-content: center; gap: 10px;
    font-family: "Montserrat", sans-serif; font-weight: 700;
    font-size: 35px; color: var(--white);
  }
  .contact-bar__icon { width: 34px; height: 34px; flex: none; }
  .contact-bar__divider { font-weight: 500; margin: 0 2px; }

  .footer-line {
    position: absolute; left: 0; top: 415px; width: 960px; height: 65px;
    display: flex; align-items: center; justify-content: center; gap: 12px;
    font-family: "Montserrat", sans-serif; font-size: 24px;
    font-weight: 500; color: var(--grey-text);
  }
  .footer-line__highlight {
    position: relative; color: var(--green-brand); font-weight: 700;
    padding-bottom: 4px; border-bottom: 1.5px solid var(--green-brand);
  }
  .footer-line__highlight::after {
    content: ""; position: absolute; left: 50%; bottom: -8px;
    margin-left: -6px;
    border-left: 6px solid transparent; border-right: 6px solid transparent;
    border-top: 7px solid var(--green-brand);
  }
</style>
</head>
<body>
  <div class="billboard">
    <svg class="billboard__shapes" width="960" height="267" viewBox="0 0 960 267">
      <defs>
        <linearGradient id="backdropTone" x1="0" y1="0" x2="0" y2="1">
          <stop offset="0" stop-color="#e7e7e5"/>
          <stop offset="0.62" stop-color="#cfcdc8"/>
          <stop offset="0.68" stop-color="#7a5738"/>
          <stop offset="1" stop-color="#5a3e29"/>
        </linearGradient>
        <radialGradient id="bagTone" cx="0.5" cy="0.5" r="0.5">
          <stop offset="0" stop-color="#9b8f7c"/>
          <stop offset="1" stop-color="#9b8f7c" stop-opacity="0"/>
        </radialGradient>
        <linearGradient id="bandTone" x1="0" y1="0" x2="1" y2="0">
          <stop offset="0" stop-color="#0a6242"/>
          <stop offset="0.55" stop-color="#078552"/>
          <stop offset="1" stop-color="#00a063"/>
        </linearGradient>
      </defs>
      <g role="img" aria-label="Photo of a burlap money bag marked with a dollar sign beside rolled banknotes on a wooden table">
        <rect x="0" y="0" width="960" height="267" fill="url(#backdropTone)"/>
        <ellipse cx="820" cy="155" rx="140" ry="110" fill="url(#bagTone)"/>
      </g>
      <polygon points="0,0 336,0 373,75 0,75" fill="#ffffff"/>
      <polygon points="0,75 602,75 705,267 0,267" fill="url(#bandTone)"/>
    </svg>

    <div class="brand">
      <div class="brand__name">Keystonery</div>
      <div class="brand__tagline">Discover lasting prosperity</div>
    </div>

    <h1 class="headline">Don't spend your time<br>Worrying about your money,<br>Let us help you plan for it</h1>

    <div class="services">
      <div class="service service--planning">
        <svg class="service__icon" viewBox="0 0 54 54" aria-hidden="true">
          <circle cx="27" cy="27" r="27" fill="var(--green-brand)"/>
          <circle cx="27" cy="27" r="15" fill="none" stroke="#fff" stroke-width="2" stroke-dasharray="4 2"/>
          <circle cx="27" cy="27" r="10" fill="none" stroke="#fff" stroke-width="1.6"/>
          <text x="27" y="32" text-anchor="middle" font-family="Montserrat, sans-serif" font-weight="700" font-size="13" fill="#fff">$</text>
        </svg>
        Planning
      </div>
      <div class="service service--investments">
        <svg class="service__icon" viewBox="0 0 54 54" aria-hidden="true">
          <circle cx="27" cy="27" r="27" fill="var(--green-brand)"/>
          <circle cx="27" cy="17" r="7" fill="none" stroke="#fff" stroke-width="1.6"/>
          <text x="27" y="21" text-anchor="middle" font-family="Montserrat, sans-serif" font-weight="700" font-size="10" fill="#fff">$</text>
          <path d="M27 24 V40 M27 33 q-7 -1 -8 -7 q7 0 8 7 M27 33 q7 -1 8 -7 q-7 0 -8 7 M17 40 H37" fill="none" stroke="#fff" stroke-width="1.6"/>
        </svg>
        Investments
      </div>
      <div class="service service--taxes">
        <svg class="service__icon" viewBox="0 0 54 54" aria-hidden="true">
          <circle cx="27" cy="27" r="27" fill="var(--green-brand)"/>
          <rect x="15" y="13" width="20" height="27" fill="none" stroke="#fff" stroke-width="1.6"/>
          <text x="17" y="21" font-family="Montserrat, sans-serif" font-weight="700" font-size="7" fill="#fff">TAX</text>
          <rect x="27" y="24" width="13" height="17" fill="var(--green-brand)" stroke="#fff" stroke-width="1.6"/>
          <path d="M30 28 H37 M30 32 H37 M30 36 H37 M18 27 H24 M18 31 H24" stroke="#fff" stroke-width="1.4"/>
        </svg>
        Taxes
      </div>
      <div class="service service--insurance">
        <svg class="service__icon" viewBox="0 0 54 54" aria-hidden="true">
          <circle cx="27" cy="27" r="27" fill="var(--green-brand)"/>
          <path d="M16 24 a11 10 0 0 1 22 0 Z" fill="none" stroke="#fff" stroke-width="1.6"/>
          <path d="M27 14 V30" stroke="#fff" stroke-width="1.6"/>
          <path d="M12 36 l6 -4 h9 a2 2 0 0 1 0 4 h-6 M27 35 l9 -4 a2 2 0 0 1 2 3 l-10 6 h-10 l-4 2" fill="none" stroke="#fff" stroke-width="1.6" stroke-linejoin="round"/>
        </svg>
        Insurance
      </div>
    </div>

    <div class="contact-bar">
      <svg class="contact-bar__icon" viewBox="0 0 34 34" aria-hidden="true">
        <circle cx="17" cy="17" r="16" fill="#fff"/>
        <path d="M11 9 l4 -1 2 6 -3 2 q2 4 5 6 l2 -3 6 2 -1 4 q-10 1 -15 -16 Z" fill="var(--ink-bar)"/>
      </svg>
      <span>302-418-2907</span>
      <span class="contact-bar__divider">|</span>
      <svg class="contact-bar__icon" viewBox="0 0 34 34" aria-hidden="true">
        <circle cx="17" cy="17" r="16" fill="#fff"/>
        <g fill="none" stroke="var(--ink-bar)" stroke-width="1.6">
          <circle cx="17" cy="17" r="10"/>
          <ellipse cx="17" cy="17" rx="4.5" ry="10"/>
          <path d="M7 17 H27 M9 12 H25 M9 22 H25"/>
        </g>
      </svg>
      <span>www.keystoneryllc.example</span>
    </div>

    <p class="footer-line">
      Everything you need for your finances in this
      <span class="footer-line__highlight">Building Right Here</span>
    </p>
  </div>
</body>
</html>
```